Computer Training in the Education sector - Letterhead

We need a new letter head to be designed for the company. We provide computer training fro the Education Sector, both primary and private tertiary providers. The colours will need to tie in with the website www.crossingthestream.co.nz.
The company name is Crossing the Stream with the tag line of Computer Training for Educators.
The footer will need to have the following detail...
0508 PCS MENTOR
021 839 415
www.crossingthestream.co.nz / training@crossingthestream.co.nz
Updates

Thanks for the designs so far.

Some have watermarks in the background. Please don't worry about using watermarks as I will not be using a watermark in in a final design.
Regards,
Roger

Thank you for all the designs and the effort. There was some great concepts that came through.

Cheers
Roger

Industry/Entity Type

Computer

```html
<!DOCTYPE html>
<html lang="en">
<head>
<meta charset="utf-8">
<title>Crossing the Stream – Letterhead</title>
<link rel="stylesheet" href="https://fonts.googleapis.com/css2?family=Arimo:wght@400;700&display=swap">
<style>
  :root {
    --paper: #ffffff;
    --ink: #1f1f1f;
    --brand-blue: #2f78bf;
    --brand-orange: #e8812f;
    --brand-green: #8cbf3f;
    --tint-green: #eef4e2;
    --tint-blue: #e2eaf5;
    --rule: #9a9a9a;
  }
  * { margin: 0; padding: 0; box-sizing: border-box; }
  html, body {
    width: 1028px;
    height: 1200px;
    overflow: hidden;
    background: var(--paper);
  }
  .letterhead {
    position: relative;
    width: 1028px;
    height: 1200px;
    background: var(--paper);
    font-family: "Arimo", Arial, sans-serif;
    color: var(--ink);
  }
  .brand {
    position: absolute;
    left: 60px;
    top: 62px;
    display: flex;
    align-items: flex-start;
    gap: 10px;
  }
  .brand-dot {
    width: 16px;
    height: 16px;
    margin-top: 10px;
    border-radius: 50%;
    background: var(--brand-orange);
  }
  .brand-name {
    width: 170px;
    font-family: "Arimo", Arial, sans-serif;
    font-weight: 400;
    font-size: 30px;
    line-height: 34px;
    color: var(--brand-blue);
  }
  .tagline {
    position: absolute;
    left: 252px;
    top: 86px;
    font-weight: 700;
    font-size: 17px;
    letter-spacing: 1.6px;
    color: var(--ink);
  }
  .contact {
    position: absolute;
    left: 704px;
    top: 52px;
    height: 96px;
    padding: 1px 0 0 17px;
    border-left: 1px solid var(--rule);
    list-style: none;
    font-size: 15px;
    line-height: 24.5px;
    color: var(--ink);
  }
  .footer-backdrop {
    position: absolute;
    left: 30px;
    top: 726px;
    width: 985px;
    height: 450px;
    background:
      radial-gradient(ellipse 45% 60% at 28% 45%, var(--tint-green) 0%, rgba(238,244,226,0) 100%),
      radial-gradient(ellipse 45% 50% at 72% 72%, var(--tint-blue) 0%, rgba(226,234,245,0) 100%);
  }
</style>
</head>
<body>
  <main class="letterhead">
    <header class="letterhead-header">
      <div class="brand">
        <span class="brand-dot"></span>
        <div class="brand-name">Crossing<br>the Stream</div>
      </div>
      <p class="tagline">Computer Training for Educators</p>
      <ul class="contact">
        <li>P: 0508 PCS MENTOR</li>
        <li>F: 021 839 415</li>
        <li>E: training@crossingthestream.co.nz</li>
        <li>W: www.crossingthestream.co.nz</li>
      </ul>
    </header>
    <div class="footer-backdrop" role="img" aria-label="Faint sweeping pattern of green and blue tiles along the lower page"></div>
  </main>
</body>
</html>
```